BildeVOLD buisnesscard

Hey :) I need a modern buisnesscard for my company BildeVOLD
It most have:
Dagligleder og Fotograf: Henrik Audun Strandvik

Mob: +4791264085
Epost: post@bildevold.example
Adresse: Kvernbakken9, 6040 Langevåg

Facbook and instagram logo with text BildeVOLD

BildeVOLD logo

It Company

```html
<!DOCTYPE html>
<html lang="no">
<head>
<meta charset="utf-8">
<title>BildeVOLD – visittkort</title>
<link rel="stylesheet" href="https://fonts.googleapis.com/css2?family=Open+Sans:wght@400;600&display=swap">
<style>
  :root {
    --backdrop: #e9e7e4;
    --card: #ffffff;
    --ink: #a7a7a7;
    --card-shadow: rgba(0, 0, 0, 0.28);
  }
  * { margin: 0; padding: 0; box-sizing: border-box; }
  html, body {
    width: 1200px;
    height: 1000px;
    overflow: hidden;
    background: var(--backdrop);
    font-family: "Open Sans", Arial, sans-serif;
    color: var(--ink);
  }
  .canvas { position: relative; width: 1200px; height: 1000px; }
  .card {
    position: absolute;
    left: 266px;
    width: 666px;
    height: 397px;
    background: var(--card);
    box-shadow: 0 3px 8px var(--card-shadow);
  }
  .card--front { top: 74px; }
  .card--back { top: 533px; }

  .brand-name {
    position: absolute;
    font-weight: 600;
    color: var(--ink);
    white-space: nowrap;
    text-transform: uppercase;
  }
  .card--front .brand-name {
    left: 60px;
    top: 182px;
    font-size: 24px;
    letter-spacing: 3px;
  }
  .card--back .brand-name {
    left: 0;
    right: 0;
    top: 176px;
    text-align: center;
    font-size: 30px;
    letter-spacing: 6px;
  }

  .contact {
    position: absolute;
    left: 332px;
    top: 110px;
    font-size: 16px;
    line-height: 24px;
  }
  .contact__name {
    font-size: 17px;
    font-weight: 600;
    letter-spacing: 0.6px;
    text-transform: uppercase;
    margin-bottom: 45px;
  }
  .contact__social {
    display: flex;
    align-items: center;
    gap: 7px;
    font-size: 15px;
    text-transform: uppercase;
    margin-bottom: 11px;
  }
  .social-square {
    width: 11px;
    height: 11px;
    background: var(--ink);
  }
  .contact__row { display: flex; align-items: center; gap: 6px; }
  .contact__row svg { width: 13px; height: 13px; flex: none; }
  .icon-fill { fill: var(--ink); }
  .icon-line { fill: none; stroke: var(--card); stroke-width: 2; }
</style>
</head>
<body>
<main class="canvas">
  <section class="card card--front" aria-label="Visittkort forside">
    <div class="brand-name">BildeVOLD</div>
    <div class="contact">
      <div class="contact__name">Henrik Audun Strandvik</div>
      <div class="contact__social"><span class="social-square"></span>BildeVOLD</div>
      <div class="contact__row">
        <svg viewBox="0 0 24 24" aria-hidden="true"><path class="icon-fill" d="M6.6 10.8a15.1 15.1 0 0 0 6.6 6.6l2.2-2.2c.3-.3.7-.4 1-.2 1.1.4 2.3.6 3.6.6.6 0 1 .4 1 1V20c0 .6-.4 1-1 1A17 17 0 0 1 3 4c0-.6.4-1 1-1h3.5c.6 0 1 .4 1 1 0 1.3.2 2.5.6 3.6.1.3 0 .7-.2 1z"/></svg>
        <span>+4791264085</span>
      </div>
      <div class="contact__row">
        <svg viewBox="0 0 24 24" aria-hidden="true"><rect class="icon-fill" x="2" y="5" width="20" height="14"/><path class="icon-line" d="M3 6l9 7 9-7"/></svg>
        <span>post@bildevold.example</span>
      </div>
      <div class="contact__row"><span>Kvernbakken9, 6040 Langevåg.no</span></div>
    </div>
  </section>

  <section class="card card--back" aria-label="Visittkort bakside">
    <div class="brand-name">BildeVOLD</div>
  </section>
</main>
</body>
</html>
```